Heron Loan Partners Business Card

We need a business card design for our mortgage servicing company. In addition to servicing the loans of homeowners, we help homeowners with purchasing their homes and any mortgage refinancing. We would like to see designs that use the colors in the logo attached below (gold-ish yellow and navy blue), and any other design you deem fit! The design should communicate a simpler life with smart mortgages provided by Heron.

```html
<!DOCTYPE html>
<html lang="en">
<head>
<meta charset="UTF-8">
<title>Heron Loan Partners – Business Card</title>
<link rel="stylesheet" href="https://fonts.googleapis.com/css2?family=PT+Serif:wght@400;700&family=Poppins:wght@400&display=swap">
<style>
  :root {
    --page-bg: #e6e3e3;
    --card-light: #efe6e5;
    --card-light-deep: #e4d6d5;
    --navy: #272154;
    --gold: #dfb23c;
    --white: #ffffff;
  }
  * { margin: 0; padding: 0; box-sizing: border-box; }
  html, body {
    width: 1200px; height: 900px; overflow: hidden;
    background: var(--page-bg);
  }
  .business-card {
    position: absolute; left: 100px; top: 141px;
    width: 1000px; height: 618px; overflow: hidden;
    background: linear-gradient(160deg, var(--card-light) 0%, var(--card-light-deep) 100%);
    box-shadow: 0 12px 30px rgba(0,0,0,0.18);
  }
  .card-shapes { position: absolute; inset: 0; width: 100%; height: 100%; }
  .brand-name {
    position: absolute; left: 60px; top: 132px; width: 390px;
    text-align: center;
    font-family: "PT Serif", serif; font-weight: 700; font-size: 46px;
    color: var(--navy); letter-spacing: -0.5px; line-height: 1;
    white-space: nowrap;
  }
  .contact-block {
    position: absolute; left: 545px; top: 0; color: var(--white);
    font-family: "Poppins", sans-serif;
  }
  .person-name {
    position: absolute; top: 110px; left: 0; white-space: nowrap;
    font-family: "PT Serif", serif; font-weight: 400; font-size: 45px;
    color: var(--gold); line-height: 1;
  }
  .person-role {
    position: absolute; top: 152px; left: 0; white-space: nowrap;
    font-size: 29px; line-height: 1.2;
  }
  .address {
    position: absolute; top: 236px; left: 0; white-space: nowrap;
    font-size: 29px; line-height: 36.5px; font-style: normal;
  }
  .contact-list {
    position: absolute; top: 390px; left: 0; list-style: none;
    font-size: 29px; line-height: 36.5px; white-space: nowrap;
  }
  .contact-list li { display: flex; align-items: center; gap: 8px; }
  .contact-icon { width: 26px; height: 26px; flex: none; fill: var(--gold); }
</style>
</head>
<body>
  <div class="business-card">
    <svg class="card-shapes" viewBox="0 0 1090 674" preserveAspectRatio="none" aria-hidden="true">
      <path class="gold-wave" fill="var(--gold)"
        d="M479 0 C535 90 532 215 490 315 C455 400 440 480 455 560 C465 615 485 650 500 674 L1090 674 L1090 0 Z"/>
      <path class="navy-panel" fill="var(--navy)"
        d="M524 0 C565 90 552 215 512 315 C478 400 460 480 466 560 C470 615 488 650 502 674 L1090 674 L1090 0 Z"/>
    </svg>

    <div class="brand-name">Heron Mortgage</div>

    <div class="contact-block">
      <h1 class="person-name">Daniel Reeves</h1>
      <p class="person-role">Managing Director</p>
      <address class="address">58 Harbor Crest Lane<br>Suite 12<br>30817, Maple Bay</address>
      <ul class="contact-list">
        <li>
          <svg class="contact-icon" viewBox="0 0 24 24" aria-hidden="true"><path d="M6.6 10.8a15.2 15.2 0 0 0 6.6 6.6l2.2-2.2a1 1 0 0 1 1-.25 11.4 11.4 0 0 0 3.6.57 1 1 0 0 1 1 1V20a1 1 0 0 1-1 1A17 17 0 0 1 3 4a1 1 0 0 1 1-1h3.5a1 1 0 0 1 1 1c0 1.25.2 2.45.57 3.57a1 1 0 0 1-.25 1z"/></svg>
          <span>044-870 215 364</span>
        </li>
        <li>
          <svg class="contact-icon" viewBox="0 0 24 24" aria-hidden="true"><path d="M2 5h20v14H2z M2 5l10 8 10-8" fill="var(--gold)"/><path d="M2 6l10 8 10-8" fill="none" stroke="var(--navy)" stroke-width="1.6"/></svg>
          <span>info@heronloan.com</span>
        </li>
        <li>
          <svg class="contact-icon" viewBox="0 0 24 24" aria-hidden="true"><circle cx="12" cy="12" r="10"/><g fill="none" stroke="var(--navy)" stroke-width="1.4"><ellipse cx="12" cy="12" rx="4.5" ry="10"/><path d="M2 12h20M4 7h16M4 17h16M12 2v20"/></g></svg>
          <span>www.heronloan.com</span>
        </li>
      </ul>
    </div>
  </div>
</body>
</html>
```